Commercial Loan Originator Business Card (CHANGE COLORS SCHEME)

CHANGE COLOR SCHEME - SAME DESIGN

Name Marlene Agate
Title Commercial Loan Originator
Office (800) 417-2906 x68
Direct (240) 615-2043
Email freshgreens4life@quillbox.example

Name Dale Morrow
Office (800) 417-2906 x70
Direct (410) 392-5184
Email d.morthehomeguy@quillbox.example

Name Leonard Vasko
Office (800) 417-2906 x71
Direct (215) 463-0712
Email l.vasko41@quillbox.example

Name Gwen Halsey
Office (800) 417-2906 x
Direct (202) 548-1370
Email ghalsey63@quillbox.example

Name Mirna Ashby
Office (800) 417-2906 x72
Direct (240) 871-4526
Email tristatehomelending@quillbox.example

```html
<!DOCTYPE html>
<html lang="en">
<head>
<meta charset="UTF-8">
<title>Mirna Ashby – Commercial Loan Originator</title>
<link rel="stylesheet" href="https://fonts.googleapis.com/css2?family=Cinzel:wght@600&family=Poppins:wght@400&display=swap">
<style>
  :root {
    --page-bg: #8a8a8a;
    --card-bg: #ffffff;
    --accent: #0f6f6b;
    --accent-soft: #d4ebe8;
    --ink: #1c2a2e;
    --portrait-light: #e3d4c8;
    --portrait-mid: #6b4a3c;
    --portrait-dark: #262022;
  }
  * { margin: 0; padding: 0; box-sizing: border-box; }
  html, body {
    width: 1200px;
    height: 952px;
    overflow: hidden;
    background: var(--page-bg);
  }
  .business-card {
    position: absolute;
    left: 50px;
    top: 136px;
    width: 1100px;
    height: 680px;
    background: var(--card-bg);
    overflow: hidden;
  }
  .corner-accent {
    position: absolute;
    left: 0;
    top: 0;
  }
  .bottom-band {
    position: absolute;
    left: 0;
    bottom: 0;
    width: 100%;
    height: 17px;
    background: var(--accent);
  }
  .portrait {
    position: absolute;
    left: 656px;
    top: 49px;
    width: 444px;
    height: 614px;
    border-radius: 46% 46% 0 0 / 30% 30% 0 0;
    background: linear-gradient(180deg, var(--portrait-light) 0%, var(--portrait-mid) 38%, var(--portrait-dark) 70%);
  }
  .identity {
    position: absolute;
    left: 47px;
    top: 346px;
  }
  .name {
    font-family: "Cinzel", serif;
    font-weight: 600;
    font-size: 48px;
    line-height: 1;
    color: var(--accent);
    text-transform: uppercase;
    letter-spacing: 0.5px;
  }
  .title {
    font-family: "Poppins", sans-serif;
    font-weight: 400;
    font-size: 31px;
    line-height: 1.2;
    color: var(--ink);
    margin-top: 4px;
  }
  .contacts {
    position: absolute;
    left: 52px;
    top: 488px;
    list-style: none;
    font-family: "Poppins", sans-serif;
    font-weight: 400;
    color: var(--ink);
  }
  .contact-row {
    display: flex;
    align-items: center;
    height: 40px;
    font-size: 31px;
    white-space: nowrap;
  }
  .contact-row svg {
    width: 30px;
    height: 30px;
    margin-right: 17px;
    flex: none;
  }
  .contact-row .label {
    color: var(--accent);
    margin-left: 20px;
  }
  .contact-row.email { font-size: 25px; }
</style>
</head>
<body>
  <div class="business-card">
    <svg class="corner-accent" width="700" height="180" viewBox="0 0 700 180" aria-hidden="true">
      <polygon points="0,104 697,0 0,177" fill="var(--accent-soft)"/>
      <polygon points="0,0 697,0 0,104" fill="var(--accent)"/>
    </svg>

    <div class="portrait" role="img" aria-label="Portrait photo of Mirna Ashby, smiling, in a black ruffled top"></div>

    <div class="identity">
      <h1 class="name">Mirna Ashby</h1>
      <p class="title">Commercial Loan Originator</p>
    </div>

    <ul class="contacts">
      <li class="contact-row">
        <svg viewBox="0 0 24 24" aria-hidden="true"><path fill="none" stroke="var(--accent)" stroke-width="2" stroke-linecap="round" d="M6 3l3 3-2 3c1 3 4 6 7 7l3-2 3 3-2 3c-8 0-16-8-16-16z M14 4a6 6 0 0 1 6 6 M14 7a3 3 0 0 1 3 3"/></svg>
        <span>(800) 417-2906 x72</span>
      </li>
      <li class="contact-row">
        <svg viewBox="0 0 24 24" aria-hidden="true"><path fill="none" stroke="var(--accent)" stroke-width="2" stroke-linecap="round" d="M6 3l3 3-2 3c1 3 4 6 7 7l3-2 3 3-2 3c-8 0-16-8-16-16z M14 4a6 6 0 0 1 6 6 M14 7a3 3 0 0 1 3 3"/></svg>
        <span>(240) 871-4526</span><span class="label">(Direct )</span>
      </li>
      <li class="contact-row email">
        <svg viewBox="0 0 24 24" aria-hidden="true"><rect x="1" y="5" width="22" height="14" fill="var(--accent)"/><path d="M1 5l11 8 11-8 M1 19l8-7 M23 19l-8-7" fill="none" stroke="#fff" stroke-width="1.5"/></svg>
        <span>tristatehomelending@quillbox.example</span>
      </li>
    </ul>

    <div class="bottom-band"></div>
  </div>
</body>
</html>
```